Bramblewood Card Company Business Cards

We are a trading card store with Glimmorax, sports and other TCG cards, we need a business card design that encompasses a clean cut, modern style with a retro flare. website is bramblewoodcardco.com for reference. Can utilize a comic book era feel or a more modern outdoor feel to utilize the "Pacific Northwest" elements of tress, mountains, etc.

Industry/Entity Type

Trading cards and collectibles

Contact Information for Business Card

business name, email address, phone number, name, owner job title

Font styles to use
Sans Serif

```html
<!DOCTYPE html>
<html lang="en">
<head>
<meta charset="utf-8">
<title>Bramblewood Card Company – Business Cards</title>
<link rel="stylesheet" href="https://fonts.googleapis.com/css2?family=Open+Sans:wght@400;600;700&display=swap">
<style>
  :root {
    --backdrop: #d9d9d7;
    --paper: #fbfbfa;
    --cyan: #10b4d9;
    --slate: #666768;
    --ink: #5a5b5c;
    --white: #ffffff;
  }
  * { box-sizing: border-box; margin: 0; padding: 0; }
  html, body { width: 1200px; height: 810px; overflow: hidden; }
  body {
    background: var(--backdrop);
    font-family: "Open Sans", Arial, sans-serif;
    display: flex;
    align-items: center;
    justify-content: center;
    gap: 40px;
  }
  .card {
    width: 525px;
    height: 300px;
    position: relative;
    box-shadow: 0 6px 18px rgba(0,0,0,0.18);
  }
  .card--front { background: var(--paper); border-bottom: 3px solid var(--cyan); }
  .card--back { background: var(--cyan); }

  .brand {
    display: flex;
    align-items: center;
    gap: 10px;
    font-weight: 700;
    line-height: 1.15;
  }
  .brand__mark { flex: none; }

  .card--front .brand {
    position: absolute;
    left: 38px; top: 50%;
    transform: translateY(-50%);
    width: 210px;
    font-size: 21px;
    color: var(--slate);
  }
  .card--front .brand__mark {
    width: 14px; height: 14px;
    background: var(--slate);
  }
  .divider {
    position: absolute;
    left: 262px; top: 70px;
    width: 1.5px; height: 160px;
    background: var(--cyan);
  }
  .contact {
    position: absolute;
    left: 290px; top: 88px;
    color: var(--ink);
  }
  .contact__name { color: var(--cyan); font-weight: 700; font-size: 19px; }
  .contact__role { font-size: 12.5px; margin-bottom: 16px; }
  .contact__list { list-style: none; font-size: 12px; }
  .contact__list li { display: flex; align-items: center; gap: 8px; margin-bottom: 3px; }
  .contact__list svg { width: 11px; height: 11px; flex: none; }

  .card--back .brand {
    position: absolute;
    left: 50%; top: 112px;
    transform: translateX(-50%);
    white-space: nowrap;
    font-size: 25px;
    color: var(--white);
  }
  .card--back .brand__mark {
    width: 16px; height: 16px;
    background: var(--white);
  }
  .back__url {
    position: absolute;
    left: 0; right: 0; bottom: 48px;
    text-align: center;
    color: var(--white);
    font-size: 14px;
    letter-spacing: 0.3px;
  }
</style>
</head>
<body>
  <section class="card card--front" aria-label="Business card front">
    <div class="brand"><span class="brand__mark"></span><span>Bramblewood Card Company</span></div>
    <div class="divider"></div>
    <div class="contact">
      <p class="contact__name">Daniel Whitcombe</p>
      <p class="contact__role">Managing Director</p>
      <ul class="contact__list">
        <li>
          <svg viewBox="0 0 12 12" aria-hidden="true"><path d="M3 1 L5 3.5 L4 5 Q5.5 7.5 7 8 L8.5 7 L11 9 L9.5 11 Q4 10.5 1 3 Z" fill="var(--cyan)"/></svg>
          555.201.0148
        </li>
        <li>
          <svg viewBox="0 0 12 12" aria-hidden="true"><rect x="1" y="2.5" width="10" height="7" fill="var(--cyan)"/><path d="M1 2.5 L6 6.5 L11 2.5" stroke="#fff" stroke-width="1" fill="none"/></svg>
          info@bramblewoodcardco.com
        </li>
        <li>
          <svg viewBox="0 0 12 12" aria-hidden="true"><circle cx="6" cy="6" r="5" fill="var(--cyan)"/><path d="M1 6 H11 M6 1 V11" stroke="#fff" stroke-width="0.8"/></svg>
          www.bramblewoodcardco.com
        </li>
      </ul>
    </div>
  </section>

  <section class="card card--back" aria-label="Business card back">
    <div class="brand"><span class="brand__mark"></span><span>Bramblewood Card Company</span></div>
    <p class="back__url">www.bramblewoodcardco.com</p>
  </section>
</body>
</html>
```